Brightbay Orthodontics business card design

Need a business card design that reflects our re-branding (orthodontic office - braces) and a new partnership with a pediatric dental office. We would like to include "for adults and children" on the card as well so adults know they are welcome to get their braces here as well. Office design is modern and would like business card to reflect a modern type look. Here's the text we would like to be included on the card:

Darren Wolcott, DDS, MSD
5214 West Linden Avenue, Suite 204
Lakemont, WA 76991
555-418-2637
www.brightbayortho.example
info@brightbayortho.example

Can we add the following to the existing designs? Darren Wolcott, DDS, MSD 5214 West Linden Avenue, Suite 204 Lakemont, WA 76991 555-418-2637

Does anyone have any more vertical designs available? Thanks!

Dental

```html
<!DOCTYPE html>
<html lang="en">
<head>
<meta charset="utf-8">
<title>Brightbay Orthodontics – Business Card</title>
<link rel="stylesheet" href="https://fonts.googleapis.com/css2?family=Lato:wght@400;700;900&family=Questrial&display=swap">
<style>
  :root {
    --backdrop: #2b2b2b;
    --blue: #1570b6;
    --blue-deep: #0f5f9f;
    --band: #f3f3f3;
    --ink: #1d1d1d;
    --white: #ffffff;
    --strip-warm: #e8a23a;
    --strip-cool: #8a3fa0;
  }
  * { box-sizing: border-box; margin: 0; padding: 0; }
  html, body { width: 1200px; height: 768px; overflow: hidden; }
  body {
    background: var(--backdrop);
    display: flex; align-items: center; justify-content: center;
    font-family: "Lato", sans-serif;
  }
  .card {
    position: relative;
    width: 400px; height: 680px;
    border-radius: 22px;
    background: linear-gradient(180deg, var(--blue) 0%, var(--blue-deep) 100%);
    overflow: hidden;
  }
  .edge-strip {
    position: absolute; left: 0; width: 100%; height: 10px;
    background: linear-gradient(90deg, var(--strip-warm), var(--strip-cool));
  }
  .edge-strip--top { top: 0; }
  .edge-strip--bottom { bottom: 0; }

  .doctor {
    height: 96px;
    padding-top: 30px;
    text-align: center;
    color: var(--white);
    font-family: "Questrial", sans-serif;
  }
  .doctor__name { font-size: 24px; font-weight: 400; letter-spacing: 1.5px; }
  .doctor__title { font-size: 13px; letter-spacing: 1px; margin-top: 2px; }

  .brand-band {
    height: 250px;
    background: var(--band);
    display: flex; flex-direction: column; align-items: center; justify-content: center;
    gap: 18px;
  }
  .brand { display: flex; align-items: center; gap: 14px; }
  .brand__dot { width: 46px; height: 46px; border-radius: 50%; background: var(--blue); flex: none; }
  .brand__name { font-weight: 900; font-size: 30px; line-height: 1.05; color: var(--ink); }
  .brand__tagline { font-size: 15px; letter-spacing: 2.5px; color: var(--ink); }

  .contacts { list-style: none; padding: 40px 0 0 40px; color: var(--white); }
  .contact { display: flex; align-items: center; gap: 16px; margin-bottom: 26px; font-size: 17px; letter-spacing: .5px; }
  .contact__icon { width: 28px; height: 28px; flex: none; }
  .contact--address { align-items: flex-start; line-height: 1.5; }
</style>
</head>
<body>
  <article class="card">
    <div class="edge-strip edge-strip--top" role="img" aria-label="Decorative colour strip along the top edge"></div>

    <header class="doctor">
      <h1 class="doctor__name">Darren Wolcott</h1>
      <p class="doctor__title">DDS, MSD</p>
    </header>

    <section class="brand-band">
      <div class="brand">
        <span class="brand__dot"></span>
        <h2 class="brand__name">Brightbay<br>Orthodontics</h2>
      </div>
      <p class="brand__tagline">FOR ADULTS &amp; CHILDREN</p>
    </section>

    <ul class="contacts">
      <li class="contact">
        <svg class="contact__icon" viewBox="0 0 28 28" fill="#fff"><path d="M3 9c0-3 5-5 11-5s11 2 11 5v2h-6V9H9v2H3z"/><path d="M7 13h14l3 11H4z"/><circle cx="14" cy="18" r="3" fill="#1570b6"/></svg>
        <span>555-418-2637</span>
      </li>
      <li class="contact">
        <svg class="contact__icon" viewBox="0 0 28 28" fill="none" stroke="#fff" stroke-width="2.5"><circle cx="14" cy="14" r="11"/><ellipse cx="14" cy="14" rx="5" ry="11"/><path d="M3 14h22"/></svg>
        <span>www.brightbayortho.example</span>
      </li>
      <li class="contact">
        <svg class="contact__icon" viewBox="0 0 28 28"><rect x="2" y="6" width="24" height="16" rx="1" fill="#fff"/><path d="M2 7l12 9 12-9" fill="none" stroke="#1570b6" stroke-width="2"/></svg>
        <span>info@brightbayortho.example</span>
      </li>
      <li class="contact contact--address">
        <svg class="contact__icon" viewBox="0 0 28 28"><path d="M14 2a9 9 0 0 0-9 9c0 7 9 15 9 15s9-8 9-15a9 9 0 0 0-9-9z" fill="#fff"/><circle cx="14" cy="11" r="3.5" fill="#1570b6"/></svg>
        <span>5214 West Linden Avenue, Suite 204<br>Lakemont, WA 76991</span>
      </li>
    </ul>

    <div class="edge-strip edge-strip--bottom" role="img" aria-label="Decorative colour strip along the bottom edge"></div>
  </article>
</body>
</html>
```